SkyvornQ Business Cards and Stationary Design

Need a design for our business cards and stationary. I want to carry on the theme of the logo. I want the business cards to have a design on the back. I would like the business cards and the stationary to carry the same theme, design scheme, and branding

Target Market(s)

Airlines and Maintenance Facilities

Industry/Entity Type

Aviation

Contact Information for Business Card

Name
Position Title
Address: 4827 Trellis Hollow Road, Fort Pierce, Florida, 34951
Office Number
Mobile Number
Email
Website

Font styles to use
Serif
Sans Serif

Colors

Designer to choose colors to be used in the design.

```html
<!DOCTYPE html>
<html lang="en">
<head>
<meta charset="utf-8">
<title>SkyvornQ Business Card</title>
<link rel="stylesheet" href="https://fonts.googleapis.com/css2?family=Open+Sans:wght@400;600;700&display=swap">
<style>
  :root {
    --bg: #d9d9da;
    --card: #ffffff;
    --navy: #0c3268;
    --sky: #1a8fd9;
    --ink: #333a44;
    --white: #ffffff;
  }
  * { margin: 0; padding: 0; box-sizing: border-box; }
  html, body { width: 1200px; height: 900px; overflow: hidden; }
  body {
    background: var(--bg);
    font-family: "Open Sans", Arial, sans-serif;
    position: relative;
  }
  .card {
    position: absolute;
    left: 340px;
    width: 520px;
    height: 297px;
    background: var(--card);
    border-radius: 22px;
    box-shadow: 0 6px 18px rgba(0,0,0,0.18);
    overflow: hidden;
  }
  .card--front { top: 120px; }
  .card--back { top: 480px; }

  .front-brand {
    position: absolute;
    inset: 0;
    display: flex;
    align-items: center;
    justify-content: center;
    gap: 16px;
  }
  .front-brand__dot {
    width: 46px; height: 46px;
    border-radius: 50%;
    border: 6px solid var(--navy);
  }
  .front-brand__name {
    font-weight: 700;
    font-size: 40px;
    letter-spacing: 6px;
    color: var(--navy);
    text-transform: uppercase;
  }

  .back-band {
    position: absolute;
    left: 190px;
    right: 0;
    top: 40px;
    height: 150px;
    background: var(--navy);
  }
  .back-ring {
    position: absolute;
    left: 60px;
    top: 95px;
    width: 170px;
    height: 170px;
    border-radius: 50%;
    border: 10px solid var(--sky);
    background: var(--card);
    display: flex;
    align-items: center;
    justify-content: center;
  }
  .back-ring__name {
    font-weight: 700;
    font-size: 22px;
    color: var(--navy);
    letter-spacing: 1px;
  }
  .person {
    position: absolute;
    right: 26px;
    top: 50px;
    text-align: right;
  }
  .person__name {
    font-weight: 700;
    font-size: 17px;
    color: var(--sky);
    letter-spacing: 1px;
    text-transform: uppercase;
    line-height: 1.1;
  }
  .person__title {
    font-size: 12px;
    color: var(--white);
  }
  .contacts {
    position: absolute;
    right: 26px;
    top: 108px;
    list-style: none;
    text-align: right;
    color: var(--white);
    font-size: 12.5px;
    line-height: 17px;
  }
  .contacts li { display: flex; justify-content: flex-end; align-items: center; gap: 5px; }
  .contacts svg { width: 10px; height: 10px; fill: var(--white); }
  .address {
    position: absolute;
    right: 26px;
    top: 208px;
    text-align: right;
    font-size: 13px;
    color: var(--ink);
    line-height: 18px;
  }
</style>
</head>
<body>
  <section class="card card--front">
    <div class="front-brand">
      <span class="front-brand__dot"></span>
      <span class="front-brand__name">SkyvornQ</span>
    </div>
  </section>

  <section class="card card--back">
    <div class="back-band"></div>
    <div class="back-ring"><span class="back-ring__name">SkyvornQ</span></div>

    <div class="person">
      <p class="person__name">Marcus Ellery</p>
      <p class="person__title">Managing Director</p>
    </div>

    <ul class="contacts">
      <li>044-987 654 321
        <svg viewBox="0 0 10 10" aria-hidden="true"><path d="M2 1h2l1 2-1 1a5 5 0 0 0 2 2l1-1 2 1v2c0 1-1 1-1 1A8 8 0 0 1 1 2s0-1 1-1z"/></svg>
      </li>
      <li>044-987 654 322
        <svg viewBox="0 0 10 10" aria-hidden="true"><path d="M3 0h4a1 1 0 0 1 1 1v8a1 1 0 0 1-1 1H3a1 1 0 0 1-1-1V1a1 1 0 0 1 1-1zm0 1.5v6h4v-6z"/></svg>
      </li>
      <li>info@skyvornq.com
        <svg viewBox="0 0 10 10" aria-hidden="true"><path d="M0 2h10v6H0zm1 1 4 3 4-3v-.2H1z"/></svg>
      </li>
      <li>www.skyvornq.com
        <svg viewBox="0 0 10 10" aria-hidden="true"><circle cx="5" cy="5" r="5"/></svg>
      </li>
    </ul>

    <div class="address">
      <p>4827 Trellis Hollow Road</p>
      <p>Fort Pierce, Florida, 34951</p>
    </div>
  </section>
</body>
</html>
```